one side yoga classes, other side rental log cabin

I need a flyer to advertise yoga classes on a lake , and to describe the various styles of classes, and who they can benefit, Days Times .prices
Linked to it is a rental log cabin that can be rented privetly to families or Groups (8 max) www.kelverstonletsbay.com This also is rented to yoga teacher that would like to Hire Cabin and the Studio www.orvelinehaven.co.uk or
for Holistic weekends.

Teacher

```html
<!DOCTYPE html>
<html lang="en">
<head>
<meta charset="utf-8">
<title>Orveline Haven – Yoga Classes &amp; Retreat Flyer</title>
<link rel="stylesheet" href="https://fonts.googleapis.com/css2?family=Didact+Gothic&display=swap">
<style>
  :root {
    --navy: #1f1c5c;
    --lavender: #d9d6ec;
    --ornament: #e6e3f3;
    --text: #4a4a4a;
    --paper: #ffffff;
    --page: #ffffff;
  }
  * { box-sizing: border-box; margin: 0; padding: 0; }
  html, body { width: 1200px; height: 1000px; overflow: hidden; background: var(--page); }
  body { position: relative; font-family: "Didact Gothic", "Century Gothic", sans-serif; color: var(--text); }

  .flyer {
    position: absolute; top: 107px; width: 535px; height: 755px;
    background: var(--paper); overflow: hidden;
    box-shadow: 2px 3px 6px rgba(0,0,0,.35);
  }
  .flyer--yoga { left: 41px; }
  .flyer--retreat { left: 624px; }

  .hero { position: absolute; left: 0; top: 0; width: 535px; height: 350px; }
  .hero--studio { background: linear-gradient(180deg, #9a6b45 0%, #c9cfd3 18%, #d7dbdc 45%, #a9a7a4 70%, #8f6f52 100%); }
  .hero--lodge { background: linear-gradient(180deg, #aac3e0 0%, #e4ebf1 38%, #8c8c6a 55%, #6e7d5f 63%, #6f8aa6 75%, #4f6a88 100%); }

  .hero__title {
    position: absolute; left: 0; top: 36px; width: 100%; text-align: center;
    color: var(--navy); font-weight: 400; line-height: 60px;
    text-shadow: 0 0 4px #fff, 0 0 8px #fff;
  }
  .flyer--yoga .hero__title { font-size: 48px; letter-spacing: 6px; }
  .flyer--retreat .hero__title { font-size: 51px; letter-spacing: 6.5px; }

  .hero__tagline {
    position: absolute; left: 22px; top: 286px; color: var(--navy);
    font-size: 25px; letter-spacing: 0.9px; text-shadow: 0 0 3px #fff, 0 0 6px #fff;
  }
  .hero__services { position: absolute; left: 0; top: 284px; width: 100%; height: 34px; color: #fff; font-size: 26px; }
  .hero__services span { position: absolute; top: 0; }
  .hero__services .yoga { left: 31px; }
  .hero__services .meditation { left: 138px; }
  .hero__services .spa { left: 305px; }

  .divider { position: absolute; left: 0; top: 345px; width: 535px; height: 60px; }

  .ornament { position: absolute; z-index: 1; }
  .copy { position: absolute; z-index: 2; }

  .flyer--yoga .copy--intro { left: 30px; top: 423px; width: 266px; font-size: 11.2px; line-height: 13.45px; }
  .flyer--yoga .copy--times { left: 327px; top: 420px; width: 205px; font-size: 10.8px; line-height: 13.5px; }
  .copy--times .note { font-size: 9px; line-height: 12px; margin-top: 1px; }

  .flyer--retreat .copy--intro { left: 28px; top: 430px; width: 262px; font-size: 11.6px; line-height: 15px; }
  .flyer--retreat .copy--intro p + p { margin-top: 15px; }
  .flyer--retreat .copy--list { left: 327px; top: 428px; width: 205px; font-size: 11.4px; line-height: 15px; }
  .copy--list ul { list-style: none; margin-top: 7px; }
  .copy--list li::before { content: "• "; }

  .footer-band {
    position: absolute; left: 0; top: 686px; width: 535px; height: 69px; background: var(--lavender); z-index: 1;
  }
  .footer-rule { position: absolute; left: 0; top: 678px; width: 535px; border-top: 1px dashed var(--lavender); z-index: 1; }
  .footer-address {
    position: absolute; left: 0; top: 697px; width: 300px; text-align: center; z-index: 2;
    font-size: 10.5px; line-height: 13.7px; color: var(--navy);
  }

  .contact-circle {
    position: absolute; left: 349px; top: 574px; width: 190px; height: 190px; z-index: 3;
    border-radius: 50%; background: var(--paper); text-align: center; color: var(--navy);
    padding-top: 72px;
  }
  .contact-circle .name { font-size: 20px; line-height: 24px; }
  .contact-circle .phone { font-size: 21px; line-height: 26px; letter-spacing: 1px; margin-top: 2px; }

  .gazebo-photo {
    position: absolute; left: 351px; top: 561px; width: 190px; height: 190px; border-radius: 50%; z-index: 3;
    background: linear-gradient(180deg, #cfd9e0 0%, #5a6a6f 30%, #6b5a45 60%, #b9a98e 100%);
  }
</style>
</head>
<body>

<section class="flyer flyer--yoga">
  <div class="hero hero--studio" role="img" aria-label="Photo of a yoga studio with tall lakeside windows, people practising a handstand and seated poses on mats"></div>
  <h1 class="hero__title">YOGA CLASSES</h1>
  <p class="hero__tagline">Set in a calm and relaxing lakeside studio</p>

  <svg class="divider" viewBox="0 0 535 60" aria-hidden="true">
    <line x1="0" y1="7" x2="535" y2="7" stroke="#ffffff" stroke-dasharray="3 2" opacity=".8"/>
    <rect x="0" y="10" width="535" height="19" fill="#1f1c5c"/>
    <rect x="0" y="29" width="535" height="3" fill="#fff"/>
    <rect x="0" y="32" width="535" height="20" fill="#d9d6ec"/>
    <line x1="0" y1="57" x2="535" y2="57" stroke="#d9d6ec" stroke-dasharray="3 2"/>
  </svg>

  <div class="copy copy--intro">
    <p>Yoga is significantly effective for improving wellbeing and resilience to stress in the workplace. It can reduce anxiety and fatigue, while increasing emotional well-being and resilience to stress.</p>
    <p>Orveline Haven uses Lumen Yoga in the studio and practices outside when the weather permits. It is easy-to-learn flowing movements, simple breathing techniques and effective relaxation methods.</p>
    <p>The ethos of Orveline Haven is enlightenment and positive feelings. We have a variety of sessions held throughout the week, that allow us to provide different levels of intesity, ranging from a complete beginner lesson, learning basic movements to the more advanced.</p>
    <p>We are in a perfect position to be able to invite individuals and couples to attend for more personal sessions, taking advantage of the Spa area and Zen garden during the experience.</p>
  </div>

  <div class="copy copy--times">
    <p>Class Times &amp; Price:</p>
    <p>Monday - One to One Bookings</p>
    <p>Tuesday - Hatha Yoga, 8-9am</p>
    <p>Tuesday - Lumen Yoga, 10-11.15am</p>
    <p>Tuesday - Hatha Yoga,7-8pm</p>
    <p>Friday -&nbsp; Hatha Yoga, 10-11.15am</p>
    <p>£17 per Session</p>
    <p class="note">We run a number of retreats monthly/annually.<br>Please contact me for further information.</p>
  </div>

  <div class="ornament" style="left:314px;top:548px;width:221px;height:140px;background:radial-gradient(ellipse at 62% 80%, var(--ornament) 0 50%, rgba(230,227,243,0) 75%);" role="img" aria-label="Decorative lavender floral flourish"></div>

  <div class="footer-rule"></div>
  <div class="footer-band"></div>
  <p class="footer-address">Orveline Haven, 7 Harrowmere Lakes, Harrowmere HM41 2QA<br>Tel:&nbsp; 01632 960418<br>www.orvelinehaven.co.uk</p>

  <div class="contact-circle">
    <p class="name">Contact Mirelle</p>
    <p class="phone">07700 900527</p>
  </div>
</section>

<section class="flyer flyer--retreat">
  <div class="hero hero--lodge" role="img" aria-label="Photo of a timber lodge and glass cabin on the shore of a lake under a blue sky with trees"></div>
  <h1 class="hero__title">ORVELINE HAVEN</h1>
  <div class="hero__services"><span class="yoga">Yoga</span><span class="meditation">Meditation</span><span class="spa">Spa Experience</span></div>

  <svg class="divider" viewBox="0 0 535 60" aria-hidden="true">
    <line x1="0" y1="7" x2="535" y2="7" stroke="#ffffff" stroke-dasharray="3 2" opacity=".8"/>
    <rect x="0" y="10" width="535" height="19" fill="#1f1c5c"/>
    <rect x="0" y="29" width="535" height="3" fill="#fff"/>
    <rect x="0" y="32" width="535" height="20" fill="#d9d6ec"/>
    <line x1="0" y1="57" x2="535" y2="57" stroke="#d9d6ec" stroke-dasharray="3 2"/>
  </svg>

  <div class="copy copy--intro">
    <p>Orveline Haven is located on the shores of Harrowmere Lakes, near Elmbury, Norfolk.&nbsp; The retreat enjoys the surroundings of some of the most spectacular views in the UK with a bird and wildfowl sanctuary on our doorstep - perfect to relax and unwind for a few days away.</p>
    <p>The cabin is warm, spacious and very homely with a very friendly welcome that is extended to all our guests.&nbsp; Enjoy home cooked food from the best local produce, relax in the hot tub overlooking the lake and clear your mind in the Zen Gardens and African mediation areas.</p>
  </div>

  <div class="copy copy--list">
    <p>Perfect Retreat for:</p>
    <ul>
      <li>1 day &amp; Extended Courses</li>
      <li>Walking Groups &amp; Teambuilding</li>
      <li>All levels of Yoga</li>
      <li>Relaxation groups</li>
      <li>Artists &amp; Birdwatching groups</li>
      <li>Hen Nights</li>
    </ul>
  </div>

  <div class="ornament" style="left:291px;top:545px;width:244px;height:210px;background:radial-gradient(ellipse at 65% 60%, var(--ornament) 0 50%, rgba(230,227,243,0) 75%);" role="img" aria-label="Decorative lavender floral flourish"></div>

  <div class="footer-rule"></div>
  <div class="footer-band"></div>
  <p class="footer-address">Orveline Haven, 7 Harrowmere Lakes, Harrowmere HM41 2QA<br>Tel:&nbsp; 01632 960418<br>www.orvelinehaven.co.uk</p>

  <div class="gazebo-photo" role="img" aria-label="Round photo of a wooden gazebo with a dark roof beside the lake"></div>
</section>

</body>
</html>
```